Business Card Design (NEW FILES)

ATTENTION: New vector files are available. Please update your design to reflect/use the new (better resolution) logo images.

Seeking a unique and professional business card design for a commercial drone photography/videography business. The layout should feature
the logo (attached) and include the following information:
Owen Tarrick
614-502-7738
www.skylarkreelworks.example
NRD Certified Remote Pilot

Owen Tarrick

```html
<!DOCTYPE html>
<html lang="en">
<head>
<meta charset="utf-8">
<title>Skylark Reelworks – Business Card</title>
<link href="https://fonts.googleapis.com/css2?family=Open+Sans:wght@400;600;700;800&display=swap" rel="stylesheet">
<style>
  :root {
    --backdrop: #222222;
    --navy: #1a1a4e;
    --orange: #e5864f;
    --orange-deep: #c96b36;
    --white: #ffffff;
  }
  * { box-sizing: border-box; margin: 0; padding: 0; }
  html, body { width: 1200px; height: 780px; overflow: hidden; }
  body {
    background: var(--backdrop);
    font-family: "Open Sans", Arial, sans-serif;
    position: relative;
  }
  .card {
    position: absolute;
    top: 235px;
    width: 540px;
    height: 310px;
    border-radius: 22px;
    overflow: hidden;
  }
  .card--front { left: 40px; background: var(--navy); color: var(--white); }
  .card--back { left: 620px; background: var(--orange); }

  .accent-band { position: absolute; width: 10px; height: 92px; background: var(--orange); }
  .accent-band--top { left: 0; top: 30px; }
  .accent-band--bottom { right: 0; bottom: 22px; }

  .divider { position: absolute; left: 0; top: 0; }

  .brand {
    position: absolute;
    display: flex;
    align-items: center;
    gap: 8px;
    font-weight: 600;
    letter-spacing: 1px;
    text-transform: uppercase;
  }
  .card--front .brand { left: 42px; top: 78px; font-size: 17px; line-height: 1.15; color: var(--white); }
  .brand__dot { width: 14px; height: 14px; border-radius: 50%; background: var(--orange); flex: none; }

  .credentials {
    position: absolute;
    left: 30px;
    top: 208px;
    width: 230px;
    text-align: center;
    font-size: 13px;
    line-height: 1.5;
  }

  .contact { position: absolute; left: 308px; top: 114px; }
  .contact__name { font-size: 28px; font-weight: 800; line-height: 1.05; }
  .contact__first { color: var(--orange); }
  .contact__role { font-size: 13px; margin-top: 1px; }
  .contact__list { list-style: none; margin-top: 18px; font-size: 12.5px; }
  .contact__list li { display: flex; align-items: center; gap: 8px; margin-bottom: 7px; }
  .contact__list svg { width: 12px; height: 12px; flex: none; }

  .card--back .brand {
    left: 0; right: 0; top: 0; bottom: 0;
    justify-content: center;
    font-size: 30px;
    color: var(--orange-deep);
  }
  .card--back .brand__dot { width: 24px; height: 24px; background: var(--navy); }
</style>
</head>
<body>
  <section class="card card--front">
    <div class="accent-band accent-band--top"></div>
    <div class="accent-band accent-band--bottom"></div>
    <svg class="divider" width="540" height="310" aria-hidden="true">
      <line x1="292" y1="118" x2="232" y2="218" stroke="#e5864f" stroke-width="1.2"/>
    </svg>

    <div class="brand"><span>Skylark<br>Reelworks</span><span class="brand__dot"></span></div>

    <p class="credentials">NRD Certified Remote Pilot<br>Fully Insured</p>

    <div class="contact">
      <h1 class="contact__name"><span class="contact__first">Owen</span> Tarrick</h1>
      <p class="contact__role">Owner</p>
      <ul class="contact__list">
        <li>
          <svg viewBox="0 0 24 24" aria-hidden="true"><path fill="#e5864f" d="M6.6 10.8a15.1 15.1 0 0 0 6.6 6.6l2.2-2.2a1 1 0 0 1 1-.25 11.4 11.4 0 0 0 3.6.57 1 1 0 0 1 1 1V20a1 1 0 0 1-1 1A17 17 0 0 1 3 4a1 1 0 0 1 1-1h3.5a1 1 0 0 1 1 1c0 1.25.2 2.45.57 3.57a1 1 0 0 1-.25 1z"/></svg>
          614-502-7738
        </li>
        <li>
          <svg viewBox="0 0 24 24" aria-hidden="true"><circle cx="12" cy="12" r="10" fill="none" stroke="#e5864f" stroke-width="2.4"/><path d="M2 12h20M12 2c3 3 3 17 0 20M12 2c-3 3-3 17 0 20" fill="none" stroke="#e5864f" stroke-width="1.8"/></svg>
          www.skylarkreelworks.example
        </li>
      </ul>
    </div>
  </section>

  <section class="card card--back">
    <div class="brand"><span>Skylark Reelworks</span><span class="brand__dot"></span></div>
  </section>
</body>
</html>
```